KESTREL Academy Exhibit Booth Posters

My company is KESTREL Academy (a division of KESTREL for Growth). We are exhibiting in a month, and I need to re-do my exhibit booth posters. There will be a total of 4 posters needed. Sizes are below.
1) Top- 11 feet long X 12 inches wide (Try to match color scheme in example photo)
2) Center- 4 feet long X 2 feet wide (Chalkboard background)
3) Left- 18 inches long X 2 feet wide (Cork-board back ground with the use of push pins holding up post-it-notes, paper, etc.)
4) Right- 18 inches long X 2 feet wide (Cork-board back ground with the use of push pins holding up post-it-notes, paper, etc.)
I have attached a photo of my old booth. This will get you an idea of the size, color schemes, and more. I have created basic rendering of each poster. The content is important, but the look and design should be drastically improved.
The websites to look into for ideas are:
www.kestrelforgrowth.example
www.kestrelacademy.example
Updates
I've added a new file. It's a .JPG of the certification diploma. Thanks!
Target Market(s)
Business Owners, Managers, HR, Supervisors, Teens who want to boost their resume
Industry/Entity Type
It Company
Look and feel

```html
<!DOCTYPE html>
<html lang="en">
<head>
<meta charset="utf-8">
<title>KESTREL Academy – Employer Feedback Poster</title>
<link rel="stylesheet" href="https://fonts.googleapis.com/css2?family=Francois+One&family=Gochi+Hand&display=swap">
<style>
  :root {
    --wood-dark: #7a3a14;
    --wood-mid: #b4632b;
    --wood-light: #d88a4a;
    --cork-light: #d39a5c;
    --cork-mid: #c1844a;
    --cork-dark: #a86c36;
    --label-paper: #eeedd8;
    --ink: #111111;
    --sheet: #f8f8f5;
    --sheet-back: #eeeeea;
    --note-yellow: #f2ee55;
    --note-edge: #e4dc3c;
  }
  * { box-sizing: border-box; margin: 0; padding: 0; }
  html, body { width: 900px; height: 1200px; overflow: hidden; background: #ffffff; }

  .poster {
    position: relative;
    width: 900px;
    height: 1200px;
    overflow: hidden;
    background: linear-gradient(135deg, var(--wood-light), var(--wood-mid) 45%, var(--wood-dark));
  }
  .frame-bevel {
    position: absolute;
    inset: 0;
    box-shadow: inset 0 0 0 2px rgba(0,0,0,0.35);
  }
  .cork-board {
    position: absolute;
    left: 36px; top: 36px;
    width: 828px; height: 1128px;
    background: radial-gradient(ellipse at 40% 35%, var(--cork-light), var(--cork-mid) 60%, var(--cork-dark));
    box-shadow: inset 0 0 18px rgba(0,0,0,0.55);
  }

  /* header label */
  .header-label {
    position: absolute;
    left: 84px; top: 74px;
    width: 760px; height: 272px;
    background: var(--label-paper);
    transform: rotate(-1.5deg);
    box-shadow: 3px 6px 10px rgba(0,0,0,0.35);
    display: flex;
    justify-content: center;
    align-items: center;
  }
  .header-title {
    font-family: "Francois One", "Arial Narrow", sans-serif;
    font-weight: 400;
    font-size: 78px;
    line-height: 104px;
    letter-spacing: 3px;
    color: var(--ink);
    text-align: center;
  }

  /* notebook area (flat placeholder) */
  .notebook {
    position: absolute;
    left: 0; top: 0;
    width: 900px; height: 1200px;
  }
  .notebook-page {
    position: absolute;
    width: 620px; height: 770px;
  }
  .notebook-page--back {
    left: 150px; top: 360px;
    background: var(--sheet-back);
    transform: rotate(5deg);
    box-shadow: 3px 6px 10px rgba(0,0,0,0.3);
  }
  .notebook-page--front {
    left: 110px; top: 345px;
    background: var(--sheet);
    transform: rotate(3deg);
    box-shadow: 4px 8px 14px rgba(0,0,0,0.35);
  }

  .feedback-list {
    position: absolute;
    left: 190px; top: 395px;
    width: 520px;
    list-style: none;
    font-family: "Gochi Hand", "Comic Sans MS", cursive;
    font-size: 60px;
    line-height: 76px;
    color: var(--ink);
    transform: rotate(4deg);
    transform-origin: top left;
  }
  .feedback-item {
    position: relative;
    padding-left: 84px;
    margin-bottom: 32px;
  }
  .feedback-item::before {
    content: "*";
    position: absolute;
    left: 6px; top: 6px;
  }
  .feedback-item--more {
    font-size: 38px;
    padding-left: 46px;
    margin-top: 4px;
    line-height: 60px;
  }
  .feedback-item--more::before { left: 0; top: 2px; font-size: 54px; }

  /* sticky note (flat) */
  .sticky-note {
    position: absolute;
    left: 534px; top: 806px;
    width: 306px; height: 210px;
    background: linear-gradient(160deg, var(--note-yellow), var(--note-edge));
    transform: rotate(-10deg);
    box-shadow: 4px 8px 12px rgba(0,0,0,0.35);
    text-align: center;
    font-family: "Gochi Hand", "Comic Sans MS", cursive;
    color: var(--ink);
    padding-top: 16px;
  }
  .sticky-kicker { font-size: 28px; line-height: 36px; letter-spacing: 1px; }
  .sticky-headline { font-size: 36px; line-height: 38px; font-weight: 400; letter-spacing: 3px; }
</style>
</head>
<body>
  <main class="poster">
    <div class="frame-bevel"></div>
    <div class="cork-board" role="img" aria-label="Cork board background"></div>

    <section class="header-label">
      <h1 class="header-title">CONTENT BASED ON<br>EMPLOYER FEEDBACK</h1>
    </section>

    <div class="notebook" role="img" aria-label="Spiral notebook pages pinned to the cork board">
      <div class="notebook-page notebook-page--back"></div>
      <div class="notebook-page notebook-page--front"></div>
    </div>

    <ul class="feedback-list">
      <li class="feedback-item">It’s more than<br>a paycheck</li>
      <li class="feedback-item">It’s all about<br>ATTITUDE</li>
      <li class="feedback-item">Play by<br>the rules</li>
      <li class="feedback-item feedback-item--more">AND MUCH MORE…</li>
    </ul>

    <aside class="sticky-note" aria-label="Sticky note">
      <p class="sticky-kicker">COMING SOON…</p>
      <p class="sticky-headline">WEB BASED<br>MANAGER &amp;<br>SUPERVISOR<br>TRAINING!</p>
    </aside>
  </main>
</body>
</html>
```